Animal Eye Clinic needs a Business card

We are a new veterinary ophthalmology practice (Ridgeline Pet Vision Care) and we need a business card designed. We only see animal eyes - we are not a regular veterinary clinic. We already have a logo. We are looking for a professional, good looking business card to hand out to our clients. We are looking for something simple but professional and contemporary. Our logo is likely the only picture/graphic that needs to be on the card.
Updates

Contact Information for Business Card

Delia Vossman, BSc, DVM, MSc, DipACVO
Veterinary Ophthalmologist

Phone: 250.418.3927
Email: ridgelinepetvisioncare@mailbox-example.net
Website: ridgelinepetvisioncare-example.net
Address: 1874 Thornbury Rd
Kelowna, BC, V1X 4M9

Colors

Designer to choose colors to be used in the design.

Requirements
Must have
• Our logo (attached)

```html
<!DOCTYPE html>
<html lang="en">
<head>
<meta charset="utf-8">
<title>Ridgeline Pet Vision Care – Business Card</title>
<link href="https://fonts.googleapis.com/css2?family=Lato:wght@400;700&family=Montserrat:wght@700&display=swap" rel="stylesheet">
<style>
  :root {
    --teal: #1596a8;
    --teal-dark: #0f7f90;
    --blue: #2a8fd0;
    --ink: #2b2b2b;
    --charcoal: #3a3a3a;
    --paper: #ffffff;
    --backdrop: #2e2e30;
  }
  * { box-sizing: border-box; margin: 0; padding: 0; }
  html, body {
    width: 1200px; height: 997px; overflow: hidden;
    background: var(--backdrop);
    font-family: "Lato", sans-serif;
  }
  .stage {
    position: relative; width: 1200px; height: 997px;
    display: flex; align-items: center; justify-content: center; gap: 40px;
  }
  .card {
    position: relative; width: 540px; height: 309px; overflow: hidden;
    box-shadow: 0 14px 30px rgba(0,0,0,.45);
  }
  .card--back {
    background: linear-gradient(135deg, #19a2b3, var(--teal-dark));
    color: var(--paper);
  }
  .card--front { background: var(--paper); color: var(--ink); }

  .brand { position: absolute; display: flex; align-items: center; gap: 14px; }
  .brand__mark { width: 54px; height: 54px; border-radius: 50%; flex: none; }
  .brand__name {
    font-family: "Montserrat", sans-serif; font-weight: 700;
    font-size: 23px; line-height: 1.1; letter-spacing: .5px; text-transform: uppercase;
  }
  .card--back .brand { left: 70px; top: 108px; }
  .card--back .brand__mark { background: var(--paper); }
  .card--back .brand__name { color: var(--paper); width: 300px; }
  .card--back .website {
    position: absolute; left: 140px; top: 210px;
    font-weight: 700; font-size: 13px; letter-spacing: .6px; color: var(--paper);
  }

  .card--front .brand { left: 84px; top: 42px; }
  .card--front .brand__mark { background: var(--teal); }
  .card--front .brand__name { color: var(--teal); width: 300px; }

  .divider { position: absolute; left: 0; top: 0; }

  .person { position: absolute; left: 44px; top: 140px; }
  .person__name {
    color: var(--blue); font-weight: 700; font-size: 17px; letter-spacing: .4px;
    text-transform: uppercase;
  }
  .person__role { font-size: 12px; line-height: 1.3; color: var(--ink); }

  .contact { position: absolute; left: 44px; top: 214px; list-style: none; }
  .contact li {
    display: flex; align-items: center; gap: 8px;
    font-size: 12.5px; margin-bottom: 6px; color: var(--ink);
  }
  .contact svg { flex: none; }

  .address {
    position: absolute; right: 30px; top: 128px;
    text-align: right; font-size: 12px; line-height: 1.45; color: var(--ink);
  }
  .footer-band { position: absolute; left: 0; bottom: 0; }
  .card--front .website {
    position: absolute; right: 24px; top: 196px;
    font-weight: 700; font-size: 12px; letter-spacing: .4px; color: var(--paper);
  }
</style>
</head>
<body>
<main class="stage">

  <section class="card card--back" aria-label="Business card back">
    <div class="brand">
      <span class="brand__mark"></span>
      <span class="brand__name">Ridgeline Pet Vision Care</span>
    </div>
    <p class="website">www.ridgelinepetvisioncare-example.net</p>
  </section>

  <section class="card card--front" aria-label="Business card front">
    <div class="brand">
      <span class="brand__mark"></span>
      <span class="brand__name">Ridgeline Pet Vision Care</span>
    </div>

    <svg class="divider" width="540" height="309" viewBox="0 0 540 309" aria-hidden="true">
      <line x1="44" y1="122" x2="510" y2="122" stroke="var(--blue)" stroke-width="1.5"/>
      <line x1="44" y1="200" x2="220" y2="200" stroke="var(--blue)" stroke-width="1.5"/>
    </svg>

    <div class="person">
      <p class="person__name">Delia Vossman</p>
      <p class="person__role">BSc, DVM, MSc, DipACVO</p>
      <p class="person__role">Veterinary Ophthalmologist</p>
    </div>

    <ul class="contact">
      <li>
        <svg width="14" height="14" viewBox="0 0 14 14" aria-hidden="true">
          <circle cx="7" cy="7" r="7" fill="var(--blue)"/>
          <path d="M4 5.2c0-.7.5-1.2 1.2-1.2h3.6c.7 0 1.2.5 1.2 1.2v.6H8.4v-.5H5.6v.5H4zM4.2 6.4h5.6l.4 3.4H3.8z" fill="#fff"/>
        </svg>
        250.418.3927
      </li>
      <li>
        <svg width="14" height="14" viewBox="0 0 14 14" aria-hidden="true">
          <circle cx="7" cy="7" r="7" fill="var(--blue)"/>
          <rect x="3.5" y="4.5" width="7" height="5" fill="none" stroke="#fff" stroke-width="1"/>
          <path d="M3.5 4.5 7 7.3l3.5-2.8" fill="none" stroke="#fff" stroke-width="1"/>
        </svg>
        ridgelinepetvisioncare@mailbox-example.net
      </li>
    </ul>

    <address class="address" style="font-style:normal">
      1874 Thornbury Rd,<br>Kelowna, BC, V1X 4M9
    </address>

    <svg class="footer-band" width="540" height="130" viewBox="0 0 540 130" aria-hidden="true">
      <path d="M0 130V122H300L340 90C346 85 350 84 360 84H540V130Z" fill="var(--teal)"/>
      <path d="M0 118H290L312 100H326L300 114H0Z" fill="var(--charcoal)"/>
    </svg>
    <p class="website">www.ridgelinepetvisioncare-example.net</p>
  </section>

</main>
</body>
</html>
```